Transform Your Giving

I need a tri-fold brochure that will fit in a standard number 10 business envelope. Meadowlark and Allied Services is a charitable nonprofit. The goal of this brochure is to stimulate people into thinking about other ways to make a donation. The design should communicate the essential information on donation options, create a sense of professional integrity, be graphically sharp, easy to read and laid out in a way that doesn't make the material appear crowded.

```html
<!DOCTYPE html>
<html lang="en">
<head>
<meta charset="utf-8">
<title>Transform Your Giving – Meadowlark and Allied Services</title>
<link href="https://fonts.googleapis.com/css2?family=Bebas+Neue&family=Montserrat:ital,wght@0,400;0,500;0,600;0,700;0,800;1,500;1,700&display=swap" rel="stylesheet">
<style>
:root{
  --purple:#2e2474;
  --purple-deep:#231a5e;
  --purple-light:#4a3a9e;
  --green:#3db54a;
  --green-dark:#2f9a3b;
  --ink:#1d1d24;
  --white:#ffffff;
  --page:#ffffff;
}
*{box-sizing:border-box;margin:0;padding:0}
html,body{width:720px;height:1200px;overflow:hidden;background:var(--page)}
body{position:relative;font-family:"Montserrat",Arial,sans-serif;color:var(--ink)}
.sheet{position:absolute;background:var(--white);box-shadow:0 1px 4px rgba(0,0,0,.18);overflow:hidden}
.sheet--outside{left:58px;top:101px;width:609px;height:470px}
.sheet--inside{left:53px;top:642px;width:615px;height:475px}
.panel{position:absolute;top:0;height:100%;overflow:hidden}
.abs{position:absolute}
.body-copy{font-size:6.1px;line-height:7.4px;font-weight:500}
.photo{position:absolute}
.curve{position:absolute;left:0;top:0}

/* outside: impact panel */
.impact-photo{left:0;top:0;width:202px;height:335px;background:linear-gradient(160deg,#9aa86a 0%,#c9b48a 30%,#e9c7c0 55%,#d8a8a6 75%,#8f9a64 100%)}
.impact-band{left:0;top:311px;width:140px;height:21px;background:var(--purple);border-radius:0 11px 11px 0;color:var(--white);font-family:"Bebas Neue",Impact,sans-serif;font-size:15.5px;line-height:22px;padding-left:14px;letter-spacing:.2px}
.impact-copy{left:14px;top:344px;width:180px}
.option-list{left:14px;top:398px;list-style:none;font-size:5.9px;font-weight:700}
.option-list li{height:13px;display:flex;align-items:center;gap:4px}
.tick-box{width:5px;height:5px}

/* outside: contact panel */
.contact-panel{background:linear-gradient(180deg,var(--purple) 0%,#3b2f8f 45%,var(--purple) 100%);color:var(--white);text-align:center}
.contact-intro{left:12px;top:16px;width:179px;font-size:5.8px;line-height:7.4px;font-weight:500}
.quote-card{left:15px;top:65px;width:175px;height:60px;background:var(--white);border-radius:12px}
.quote-text{left:6px;top:23px;width:160px;text-align:left;color:var(--purple);font-size:7.6px;line-height:9px;font-style:italic;font-weight:500}
.quote-text b{font-weight:700}
.quote-mark{font-family:"Bebas Neue",Impact,sans-serif;color:var(--green);font-size:24px;line-height:24px}
.brand-name{font-weight:800;letter-spacing:.3px}
.contact-brand{left:0;top:143px;width:203px;display:flex;align-items:center;justify-content:center;gap:6px;color:var(--white);font-size:11px;line-height:13px;text-align:left}
.brand-dot{width:9px;height:9px;border-radius:50%;background:var(--green)}
.will-pill{left:27px;top:195px;width:151px;height:29px;background:var(--green);border-radius:8px;font-size:5.7px;line-height:7.4px;font-weight:600;padding-top:4px}
.contact-title{left:0;top:250px;width:203px;font-size:7.8px;font-weight:700;text-decoration:underline;letter-spacing:.3px}
.contact-line{left:0;width:203px;font-size:5.8px;line-height:7.4px;font-weight:500}
.contact-icon{left:97px;width:9px;height:9px}
.follow-title{left:0;top:398px;width:203px;font-size:7.8px;font-weight:700;text-decoration:underline}
.social-row{left:71px;top:412px;width:61px;height:11px}
.disclaimer{left:18px;top:437px;width:167px;font-size:3.4px;line-height:4.4px}

/* outside: cover panel */
.cover-title{left:0;top:12px;width:203px;text-align:center;font-family:"Bebas Neue",Impact,sans-serif;color:var(--green);font-size:23.5px;line-height:24px;letter-spacing:.2px}
.cover-pill{left:21px;top:38px;width:163px;height:14px;background:var(--purple);border-radius:7px;color:var(--white);font-size:10px;line-height:14px;font-weight:700;text-align:center;letter-spacing:.3px}
.cover-lede{left:0;top:56px;width:203px;text-align:center;font-size:8.3px;line-height:10px;font-weight:400}
.cover-photo{left:0;top:78px;width:203px;height:345px;background:linear-gradient(170deg,#6f7c4a 0%,#b39a63 25%,#c98f58 45%,#e0e3ef 60%,#5d78b4 75%,#87704c 100%)}
.bubble{width:50px;height:50px;border-radius:50%;background:radial-gradient(circle at 40% 35%,rgba(255,255,255,.92),rgba(232,230,245,.75));box-shadow:0 0 6px rgba(255,255,255,.9);display:flex;flex-direction:column;align-items:center;justify-content:center;color:var(--purple);font-size:5.6px;line-height:6px;font-weight:700;text-align:center}
.bubble svg{margin-bottom:2px}
.cover-brand{left:0;top:424px;width:203px;display:flex;align-items:center;justify-content:center;gap:6px;color:var(--purple);font-size:12px;line-height:13px}

/* inside */
.option-icon{position:absolute}
.option-heading{color:var(--purple);font-size:7.8px;line-height:9.4px;font-weight:700}
.option-sub{color:var(--purple);font-size:5.9px;line-height:7.4px;font-weight:700;font-style:italic}
.how-pill{position:absolute;width:98px;height:12px;background:var(--green);border-radius:6px;color:var(--white);font-size:7.2px;line-height:12px;font-weight:700;padding-left:5px;letter-spacing:.3px}
.check-item{display:flex;gap:5px}
.check-item svg{flex:none;margin-top:1px}
.couple-photo{left:0;top:390px;width:206px;height:85px;background:linear-gradient(100deg,#6f9a3e 0%,#a9b86b 35%,#d9c8a0 55%,#7fa24a 100%)}
.qcd-panel{background:linear-gradient(180deg,#e7e5ea 0%,#cfcbd6 30%,#8f88b2 47%,#3f318c 60%,var(--purple) 100%);color:var(--white)}
.qcd-photo{left:0;top:0;width:204px;height:240px;background:linear-gradient(180deg,#ecebef 0%,#d6d3da 40%,#a9a6b8 70%,rgba(63,49,140,0) 100%)}
.qcd-panel .option-heading,.qcd-panel .option-sub{color:var(--white)}
.site-address{right:12px;top:450px;color:var(--white);font-size:11.5px;font-weight:400}
</style>
</head>
<body>

<!-- Outside of the brochure -->
<section class="sheet sheet--outside">

  <div class="panel impact-panel" style="left:0;width:202px">
    <div class="photo impact-photo" role="img" aria-label="Photo of a smiling older woman with glasses reading a book outdoors"></div>
    <svg class="curve" width="202" height="470" viewBox="0 0 202 470">
      <path d="M0 288 C40 262 110 255 202 325 L202 470 L0 470Z" fill="var(--green)"/>
      <path d="M0 300 C45 270 120 268 202 340 L202 470 L0 470Z" fill="var(--white)"/>
    </svg>
    <div class="abs impact-band">The impact of your gift</div>
    <p class="abs body-copy impact-copy">Your generosity drives our mission. With every Smart gift you're supporting Meadowlark and Allied Services. Join our community of Smart Givers today and make an enduring impact. With Smart Giving your generosity reaches further. Begin your Smart Giving journey with us today.</p>
    <ul class="abs option-list">
      <li><svg class="tick-box" viewBox="0 0 10 10"><rect x="1" y="1" width="8" height="8" fill="none" stroke="var(--purple)" stroke-width="1.2"/><path d="M2.5 5 L4.5 7 L8 3" fill="none" stroke="var(--purple)" stroke-width="1.2"/></svg>Stocks and Securities</li>
      <li><svg class="tick-box" viewBox="0 0 10 10"><rect x="1" y="1" width="8" height="8" fill="none" stroke="var(--purple)" stroke-width="1.2"/><path d="M2.5 5 L4.5 7 L8 3" fill="none" stroke="var(--purple)" stroke-width="1.2"/></svg>DAFs</li>
      <li><svg class="tick-box" viewBox="0 0 10 10"><rect x="1" y="1" width="8" height="8" fill="none" stroke="var(--purple)" stroke-width="1.2"/><path d="M2.5 5 L4.5 7 L8 3" fill="none" stroke="var(--purple)" stroke-width="1.2"/></svg>QCDs</li>
      <li><svg class="tick-box" viewBox="0 0 10 10"><rect x="1" y="1" width="8" height="8" fill="none" stroke="var(--purple)" stroke-width="1.2"/><path d="M2.5 5 L4.5 7 L8 3" fill="none" stroke="var(--purple)" stroke-width="1.2"/></svg>Crypto</li>
      <li><svg class="tick-box" viewBox="0 0 10 10"><rect x="1" y="1" width="8" height="8" fill="none" stroke="var(--purple)" stroke-width="1.2"/><path d="M2.5 5 L4.5 7 L8 3" fill="none" stroke="var(--purple)" stroke-width="1.2"/></svg>Charitable Annuity</li>
    </ul>
  </div>

  <div class="panel contact-panel" style="left:202px;width:203px">
    <p class="abs contact-intro">To learn more about Smart Giving Options and how they can benefit you and Meadowlark and Allied Services, please reach out to our team. We're here to help you navigate these giving methods and answer any question you may have.</p>
    <div class="abs quote-card">
      <div class="abs quote-mark" style="left:6px;top:2px">&ldquo;</div>
      <svg class="abs" style="left:34px;top:10px" width="138" height="40" viewBox="0 0 138 40"><path d="M0 1 H128 Q136 1 136 9 V30 Q136 38 128 38 H76" fill="none" stroke="var(--green)" stroke-width=".8"/></svg>
      <p class="abs quote-text">Being kind to others is a way of being good to yourself.<br><b>- Miriam Ostrow</b></p>
      <div class="abs quote-mark" style="left:80px;top:37px">&rdquo;</div>
    </div>
    <div class="abs contact-brand"><span class="brand-dot"></span><span class="brand-name">Meadowlark and<br>Allied Services</span></div>
    <div class="abs will-pill">If you do not have a will, go to<br>www.EasyWillPlan.org<br>In 20 minutes you can have a legal will for free.</div>
    <h2 class="abs contact-title">CONTACT US</h2>
    <p class="abs contact-line" style="top:266px">Have more question?<br>Please contact us at Meadowlark &amp; Allied Services</p>
    <svg class="abs contact-icon" style="top:287px" viewBox="0 0 10 10"><circle cx="5" cy="5" r="5" fill="var(--green)"/><path d="M5 2.2a2 2 0 0 1 2 2c0 1.5-2 3.6-2 3.6S3 5.7 3 4.2a2 2 0 0 1 2-2z" fill="var(--white)"/><circle cx="5" cy="4.2" r=".7" fill="var(--green)"/></svg>
    <p class="abs contact-line" style="top:298px">1420 Prairie View Rd.<br>Suite 2, Larkfield, ND&nbsp; 58990</p>
    <svg class="abs contact-icon" style="top:315px" viewBox="0 0 10 10"><circle cx="5" cy="5" r="5" fill="var(--green)"/><path d="M3.3 2.6l1 1-.5.8c.4.8.9 1.3 1.7 1.7l.8-.5 1 1-.6.9c-2 0-3.9-1.9-4-4z" fill="var(--white)"/></svg>
    <p class="abs contact-line" style="top:327px">555-014-2200 (ext. 100)</p>
    <svg class="abs contact-icon" style="top:338px" viewBox="0 0 10 10"><circle cx="5" cy="5" r="5" fill="var(--green)"/><rect x="2.6" y="3.3" width="4.8" height="3.4" fill="var(--white)"/><path d="M2.6 3.3 L5 5.2 L7.4 3.3" fill="none" stroke="var(--green)" stroke-width=".5"/></svg>
    <p class="abs contact-line" style="top:349px">info@meadowlarkallied.org</p>
    <svg class="abs contact-icon" style="top:361px" viewBox="0 0 10 10"><circle cx="5" cy="5" r="5" fill="var(--green)"/><circle cx="5" cy="5" r="2.6" fill="none" stroke="var(--white)" stroke-width=".6"/><path d="M2.4 5H7.6M5 2.4C3.8 4 3.8 6 5 7.6M5 2.4C6.2 4 6.2 6 5 7.6" fill="none" stroke="var(--white)" stroke-width=".5"/></svg>
    <p class="abs contact-line" style="top:372px">www.meadowlarkallied.org</p>
    <h2 class="abs follow-title">Follow us:</h2>
    <svg class="abs social-row" viewBox="0 0 61 11"><line x1="5" y1="5.5" x2="56" y2="5.5" stroke="var(--green)" stroke-width="1"/><circle cx="5.5" cy="5.5" r="5" fill="var(--green)"/><circle cx="30.5" cy="5.5" r="5" fill="var(--green)"/><circle cx="55.5" cy="5.5" r="5" fill="var(--green)"/></svg>
    <p class="abs disclaimer">This material has been prepared for informational purposes only and is not intended to provide tax, accounting, or legal advice. Meadowlark and Allied Services is not a professional fiduciary organization. Please consult with your tax advisor or financial professional before making a decision about Smart Giving.</p>
  </div>

  <div class="panel cover-panel" style="left:405px;width:204px">
    <h1 class="abs cover-title">Transform your giving</h1>
    <div class="abs cover-pill">BE STRATEGIC, BE SMART</div>
    <p class="abs cover-lede">Discover the impact of Smart Giving with<br>Meadowlark and Allied Services</p>
    <div class="photo cover-photo" role="img" aria-label="Photo of a laughing older couple walking arm in arm through an autumn park"></div>
    <svg class="curve" width="204" height="470" viewBox="0 0 204 470">
      <path d="M0 75 H204 V88 C150 115 90 120 15 92 L0 86Z" fill="var(--white)"/>
      <path d="M15 92 C90 120 150 115 204 88 V105 C140 130 80 125 15 92Z" fill="var(--green)"/>
      <path d="M0 412 C50 385 150 380 204 410 V470 H0Z" fill="var(--purple)"/>
      <path d="M0 420 C50 395 150 392 204 418 V470 H0Z" fill="var(--white)"/>
    </svg>
    <div class="abs bubble" style="left:13px;top:103px"><svg width="24" height="16" viewBox="0 0 24 16"><circle cx="7" cy="5" r="4.5" fill="none" stroke="var(--purple)" stroke-width="1.2"/><circle cx="17" cy="5" r="4.5" fill="none" stroke="var(--purple)" stroke-width="1.2"/><circle cx="12" cy="11" r="4.5" fill="var(--white)" stroke="var(--purple)" stroke-width="1.2"/></svg>Crypto</div>
    <div class="abs bubble" style="left:139px;top:132px"><svg width="22" height="20" viewBox="0 0 22 20"><circle cx="8" cy="8" r="5.5" fill="none" stroke="var(--purple)" stroke-width="2" stroke-dasharray="2 1.4"/><circle cx="15" cy="13" r="5" fill="none" stroke="var(--purple)" stroke-width="2" stroke-dasharray="2 1.4"/></svg>DAF's</div>
    <div class="abs bubble" style="left:13px;top:232px"><svg width="22" height="18" viewBox="0 0 22 18"><rect x="2" y="9" width="3" height="8" fill="var(--purple)"/><rect x="7" y="6" width="3" height="11" fill="var(--purple)"/><rect x="12" y="8" width="3" height="9" fill="var(--purple)"/><rect x="17" y="3" width="3" height="14" fill="var(--purple)"/><path d="M1 6 L7 2 L12 5 L20 0" fill="none" stroke="var(--purple)" stroke-width="1"/></svg>Stocks &amp;<br>Securities</div>
    <div class="abs bubble" style="left:139px;top:261px"><svg width="18" height="18" viewBox="0 0 18 18"><rect x="1" y="5" width="16" height="4" fill="var(--purple)"/><rect x="2" y="10" width="14" height="8" fill="var(--purple)"/><rect x="8" y="5" width="2" height="13" fill="var(--white)"/><path d="M9 5 C6 0 2 2 5 5 M9 5 C12 0 16 2 13 5" fill="none" stroke="var(--purple)" stroke-width="1.2"/></svg>QCDs</div>
    <div class="abs bubble" style="left:13px;top:329px"><svg width="22" height="18" viewBox="0 0 22 18"><ellipse cx="9" cy="15" rx="6" ry="2" fill="var(--purple)"/><ellipse cx="9" cy="12" rx="6" ry="2" fill="var(--purple)"/><ellipse cx="9" cy="9" rx="6" ry="2" fill="var(--purple)"/><circle cx="17" cy="4" r="3.5" fill="var(--purple)"/></svg>Charitable<br>Annuity</div>
    <div class="abs cover-brand"><span class="brand-dot"></span><span class="brand-name">Meadowlark and<br>Allied Services</span></div>
  </div>
</section>

<!-- Inside of the brochure -->
<section class="sheet sheet--inside">

  <div class="panel" style="left:0;width:206px">
    <p class="abs body-copy" style="left:15px;top:17px;width:180px">We would like to introduce you to five Strategic and Smart ways to give that could potentially be more beneficial to you compared to traditional cash donations. We encourage you to keep this information as a guide for your future contributions.</p>
    <svg class="option-icon" style="left:15px;top:64px" width="36" height="32" viewBox="0 0 36 32"><rect x="2" y="16" width="4" height="14" fill="var(--green)"/><rect x="9" y="11" width="4" height="19" fill="var(--green)"/><rect x="16" y="14" width="4" height="16" fill="var(--green)"/><rect x="23" y="8" width="4" height="22" fill="var(--green)"/><rect x="30" y="10" width="4" height="20" fill="var(--green)"/><path d="M1 2 V31 H36" fill="none" stroke="var(--green)" stroke-width="1.6"/><path d="M3 11 L10 5 L17 9 L24 2 L32 5" fill="none" stroke="var(--green)" stroke-width="1.4"/></svg>
    <h3 class="abs option-heading" style="left:57px;top:63px;width:145px">Gifts of Stocks or Appreciated Assets Strategic &amp; Smart</h3>
    <p class="abs option-sub" style="left:57px;top:82px;width:140px">Consider your long-term publicly traded stock as a way to give to your favorite charity.</p>
    <p class="abs body-copy" style="left:15px;top:110px;width:180px">You can make a significantly bigger impact when you donate long-term appreciated securities, including stock, mutual funds, and bonds, directly to your favorite charity.</p>
    <div class="how-pill" style="left:14px;top:141px">HOW DOES IT WORK?</div>
    <p class="abs body-copy" style="left:15px;top:168px;width:180px">When you donate stock to a charity, you will generally take a tax deduction for the full market value. Because you are donating stock, your contribution and tax deduction may be significantly higher than contributing the after-tax proceeds. The same benefits apply when you donate mutual funds or bonds.</p>
    <svg class="option-icon" style="left:15px;top:234px" width="36" height="36" viewBox="0 0 36 36"><circle cx="13" cy="13" r="9" fill="none" stroke="var(--green)" stroke-width="3" stroke-dasharray="3 2"/><circle cx="13" cy="13" r="4" fill="none" stroke="var(--green)" stroke-width="1.4"/><circle cx="24" cy="24" r="8" fill="none" stroke="var(--green)" stroke-width="3" stroke-dasharray="3 2"/><circle cx="24" cy="24" r="3.5" fill="none" stroke="var(--green)" stroke-width="1.4"/></svg>
    <h3 class="abs option-heading" style="left:57px;top:234px;width:145px">Donor-Advised Fund (DAF)<br>Strategic &amp; Smart</h3>
    <p class="abs option-sub" style="left:57px;top:252px;width:140px">Consider a DAF – a simple, flexible, and tax-advantageous way to give to your favorite charities.</p>
    <p class="abs body-copy" style="left:15px;top:281px;width:180px">A Donor-Advised Fund (DAF), is like a charitable investment account for the sole purpose of supporting your favorite charities.</p>
    <div class="how-pill" style="left:14px;top:311px">HOW DOES IT WORK?</div>
    <p class="abs body-copy" style="left:15px;top:338px;width:180px">You establish a DAF and contribute cash, stocks, or non-publicly traded assets, cryptocurrency, and private company stock to be eligible for an immediate tax deduction. Those funds are contributed for tax-free growth. You can recommend grants be made from your DAF to any IRS qualified public charity.</p>
    <div class="photo couple-photo" role="img" aria-label="Photo of a happy older couple lying on the grass in a park"></div>
    <svg class="curve" width="206" height="475" viewBox="0 0 206 475">
      <path d="M0 385 H206 V475 C170 420 90 395 0 405Z" fill="var(--white)"/>
      <path d="M0 392 C90 385 170 410 206 475 H200 C165 425 90 402 0 410Z" fill="var(--purple)"/>
    </svg>
  </div>

  <div class="panel qcd-panel" style="left:206px;width:204px">
    <div class="photo qcd-photo" role="img" aria-label="Photo of an older couple on a sofa looking at a tablet together"></div>
    <svg class="option-icon" style="left:13px;top:263px" width="32" height="36" viewBox="0 0 32 36"><rect x="1" y="9" width="30" height="7" fill="var(--green)"/><rect x="3" y="18" width="26" height="18" fill="var(--green)"/><rect x="14" y="9" width="4" height="27" fill="var(--purple)"/><path d="M16 9 C11 0 4 3 9 9 M16 9 C21 0 28 3 23 9" fill="none" stroke="var(--green)" stroke-width="2"/></svg>
    <h3 class="abs option-heading" style="left:51px;top:263px;width:148px">Qualified Charitable Distributions (QCDs) Strategic &amp; Smart</h3>
    <p class="abs option-sub" style="left:51px;top:281px;width:145px">Consider a QCD – when planning your IRA withdrawal strategy...and donate to your favorite charity.</p>
    <p class="abs body-copy" style="left:13px;top:314px;width:180px">IRA owners at age 70 or over can transfer dollars from their IRA to charity tax-free each year. These transfers known as Qualified Charitable Distributions (QCDs) offer eligible older Americans a great way to easily give to charity.</p>
    <div class="how-pill" style="left:12px;top:362px">HOW DOES IT WORK?</div>
    <p class="abs body-copy" style="left:13px;top:386px;width:182px">Are you 72 and required to take a minimum distribution (RMD) from your IRA but do not need the funds? Consider a Qualified Charitable Distribution. Normally, distributions from a traditional IRA are taxable when received. With a QCD, these distributions become tax-free when paid directly from the IRA to your favorite eligible charity. An IRA owner wishing to make a QCD should contact their IRA trustee, allowing time to complete the transaction before the end of the year to receive the tax benefit.</p>
  </div>

  <div class="panel" style="left:410px;width:205px">
    <svg class="option-icon" style="left:16px;top:15px" width="34" height="26" viewBox="0 0 34 26"><circle cx="9" cy="8" r="7" fill="none" stroke="var(--green)" stroke-width="1.6"/><circle cx="25" cy="8" r="7" fill="none" stroke="var(--green)" stroke-width="1.6"/><circle cx="17" cy="18" r="7" fill="var(--white)" stroke="var(--green)" stroke-width="1.6"/><path d="M17 13 L14.5 18 L17 23 L19.5 18Z" fill="none" stroke="var(--green)" stroke-width="1"/></svg>
    <h3 class="abs option-heading" style="left:52px;top:16px;width:150px">Cryptocurrency Strategic &amp; Smart</h3>
    <p class="abs option-sub" style="left:52px;top:25px;width:150px">Consider donating Bitcoin and other cryptocurrencies to your favorite charity.</p>
    <p class="abs body-copy" style="left:14px;top:51px;width:182px">Bitcoin and other cryptocurrencies can be donated to charity just like other appreciated assets such as stocks and other business interests. Before you sell bitcoin and donate the after-tax proceeds, consider donating your bitcoin directly to a favorite charity.</p>
    <div class="how-pill" style="left:14px;top:99px">HOW DOES IT WORK?</div>
    <p class="abs body-copy" style="left:14px;top:119px;width:180px">Many donors find it useful to open a Donor-Advised Fund (DAF). This strategy includes two significant benefits, both for you and your favorite charity.</p>
    <div class="abs body-copy check-item" style="left:14px;top:153px;width:182px"><svg width="6" height="6" viewBox="0 0 10 10"><rect x="1" y="1" width="8" height="8" fill="none" stroke="var(--purple)" stroke-width="1.2"/><path d="M2.5 5 L4.5 7 L8 3" fill="none" stroke="var(--purple)" stroke-width="1.2"/></svg><span>Your tax deduction will be equal to the fair market value of the donated bitcoin (as determined by a qualified appraisal).</span></div>
    <div class="abs body-copy check-item" style="left:14px;top:183px;width:182px"><svg width="6" height="6" viewBox="0 0 10 10"><rect x="1" y="1" width="8" height="8" fill="none" stroke="var(--purple)" stroke-width="1.2"/><path d="M2.5 5 L4.5 7 L8 3" fill="none" stroke="var(--purple)" stroke-width="1.2"/></svg><span>Your cryptocurrency donation is tax-smart because it may eliminate capital gains taxes on the value /appreciation AND your favorite charity will receive 100% of the value of the contribution.</span></div>
    <p class="abs body-copy" style="left:14px;top:222px;width:180px">Often charities are not able to accept direct donations of bitcoin/crypto so using a DAF is a great way to donate these assets.</p>
    <svg class="option-icon" style="left:14px;top:258px" width="34" height="32" viewBox="0 0 34 32"><path d="M1 3 H9 M1 6 H7" stroke="var(--green)" stroke-width="1"/><path d="M4 14 C8 8 16 6 22 7" fill="none" stroke="var(--green)" stroke-width="1" stroke-dasharray="1.5 1.5"/><circle cx="26" cy="6" r="5" fill="var(--green)"/><ellipse cx="10" cy="28" rx="8" ry="2.6" fill="var(--green)"/><ellipse cx="10" cy="24" rx="8" ry="2.6" fill="var(--green)"/><ellipse cx="24" cy="28" rx="8" ry="2.6" fill="var(--green)"/><ellipse cx="24" cy="24" rx="8" ry="2.6" fill="var(--green)"/><ellipse cx="24" cy="20" rx="8" ry="2.6" fill="var(--green)"/><ellipse cx="24" cy="16" rx="8" ry="2.6" fill="var(--green)"/></svg>
    <h3 class="abs option-heading" style="left:52px;top:258px;width:150px">Charitable Gift Annuity<br>Strategic &amp; Smart</h3>
    <p class="abs option-sub" style="left:52px;top:278px;width:120px">Consider establishing a Charitable Gift Annuity</p>
    <p class="abs body-copy" style="left:14px;top:299px;width:180px">You make a donation to a single charity. The gift is set aside in a reserve account and invested.</p>
    <div class="how-pill" style="left:14px;top:324px">HOW DOES IT WORK?</div>
    <p class="abs body-copy" style="left:14px;top:343px;width:182px">A charitable gift annuity is a contract between a donor and a charity. As a donor, you make a sizable gift to charity using cash, securities, or possibly other assets. This money is then invested. In return, you become eligible to take a partial tax deduction for your donation, plus you receive a fixed stream of income from the charity for the rest of your life. At the end of your life (as well as your spouse's, if you're giving as a couple), the charity receives the remainder of the gift.</p>
    <svg class="curve" width="205" height="475" viewBox="0 0 205 475">
      <path d="M0 475 C40 430 120 418 205 415 V428 C130 430 60 440 5 475Z" fill="var(--green)"/>
      <path d="M5 475 C60 440 130 430 205 428 V475Z" fill="var(--purple)"/>
    </svg>
    <p class="abs site-address">www.meadowlarkallied.org</p>
  </div>
</section>

</body>
</html>
```